Business cards - BRENT Roofing & Siding

We need simple business cards made up for our Roofing & Siding business based in Calgary Alberta.
The logo on one side of the card and potentially our slogan "Built to last, backed by our word".
The other side could have:
-A small logo
-Rep name:
-Rep cell phone:
-Rep email:
-Office phone: 403-684-2093
-Website: PrairieShingleWorks.com

We would like to incorporate the colours from our logo, especially the lite blue on the jpeg file. I have attached the ai file and jpeg file. We like the colours better on the jpeg file.

I do not require a money back guarantee

```html
<!DOCTYPE html>
<html lang="en">
<head>
<meta charset="utf-8">
<title>BRENT Roofing &amp; Siding — Business Cards</title>
<link rel="stylesheet" href="https://fonts.googleapis.com/css2?family=Lato:wght@400;700&display=swap">
<style>
  :root {
    --backdrop: #222325;
    --card-white: #ffffff;
    --brand-blue: #078af2;
    --name-blue: #1a84e3;
    --rule-blue: #1b6fc2;
    --accent-red: #e3262a;
    --ink: #444444;
    --ink-dark: #1a1a1a;
  }
  * { box-sizing: border-box; margin: 0; padding: 0; }
  html, body { width: 1200px; height: 1200px; overflow: hidden; }
  body {
    background: var(--backdrop);
    font-family: "Lato", sans-serif;
    position: relative;
  }
  .card {
    position: absolute;
    left: 250px;
    width: 700px;
    height: 400px;
    border-radius: 26px;
  }
  .card--front { top: 170px; background: var(--card-white); }
  .card--back { top: 631px; background: var(--brand-blue); }

  .brand-lockup {
    position: absolute;
    display: flex;
    align-items: center;
    gap: 10px;
    font-weight: 400;
    white-space: nowrap;
  }
  .brand-lockup__square { display: block; flex: none; }
  .card--front .brand-lockup {
    left: 66px; top: 186px; width: 262px;
    font-size: 20px; color: var(--ink-dark);
  }
  .card--front .brand-lockup__square { width: 14px; height: 14px; background: var(--brand-blue); }
  .card--back .brand-lockup {
    left: 0; right: 0; top: 165px; justify-content: center; gap: 12px;
    font-size: 40px; color: #ffffff;
  }
  .card--back .brand-lockup__square { width: 26px; height: 26px; background: #ffffff; }

  .divider {
    position: absolute; left: 346px; top: 98px;
    width: 2px; height: 204px; background: var(--rule-blue);
  }
  .contact { position: absolute; left: 376px; top: 92px; color: var(--ink); }
  .contact__name {
    font-size: 30px; font-weight: 400; color: var(--name-blue);
    line-height: 1.1; letter-spacing: 0.2px;
  }
  .contact__title { font-size: 19px; color: var(--accent-red); margin-top: 2px; }
  .contact__address { font-size: 16.5px; line-height: 23px; margin-top: 12px; padding-left: 1px; letter-spacing: 0.3px; }
  .contact__list { list-style: none; margin-top: 10px; }
  .contact__item {
    display: flex; align-items: center; gap: 10px;
    font-size: 16.5px; line-height: 23.5px; letter-spacing: 0.3px;
  }
  .contact__icon { width: 14px; height: 14px; flex: none; fill: var(--name-blue); }

  .slogan {
    position: absolute; left: 0; right: 0; top: 342px;
    text-align: center; color: #ffffff; font-size: 20px; font-weight: 400;
    letter-spacing: 0.4px;
  }
  .slogan strong { font-weight: 700; }
</style>
</head>
<body>
  <section class="card card--front" aria-label="Business card front">
    <div class="brand-lockup"><span class="brand-lockup__square"></span>BRENT Roofing &amp; Siding</div>
    <div class="divider"></div>
    <div class="contact">
      <h1 class="contact__name">DANIEL WHITFORD</h1>
      <p class="contact__title">Managing Director</p>
      <p class="contact__address">2740 - 11 Avenue S.E. Calgary<br>Alberta T2B 0K4</p>
      <ul class="contact__list">
        <li class="contact__item">
          <svg class="contact__icon" viewBox="0 0 16 16" aria-hidden="true"><path d="M3.5 1 6 3.8 4.6 5.6c.9 2.2 2.7 4 4.8 4.8L11.2 9 14 11.5 12.6 14C7 14 2 9 2 3.4z"/></svg>
          403-684-2093
        </li>
        <li class="contact__item">
          <svg class="contact__icon" viewBox="0 0 16 16" aria-hidden="true"><path d="M4.5 1h7a1 1 0 0 1 1 1v12a1 1 0 0 1-1 1h-7a1 1 0 0 1-1-1V2a1 1 0 0 1 1-1zm.5 2v9h6V3zm3 10a.8.8 0 1 0 0 1.6A.8.8 0 0 0 8 13z"/></svg>
          403-684-2093
        </li>
        <li class="contact__item">
          <svg class="contact__icon" viewBox="0 0 16 16" aria-hidden="true"><path d="M1 3.5h14v9H1zm1.6 1 5.4 4 5.4-4z"/></svg>
          daniel@prairieshingleworks.com
        </li>
        <li class="contact__item">
          <svg class="contact__icon" viewBox="0 0 16 16" aria-hidden="true"><path d="M8 1a7 7 0 1 0 0 14A7 7 0 0 0 8 1zm0 1.5c.9 0 2 1.9 2.2 4.7H5.8C6 4.4 7.1 2.5 8 2.5zM5.8 8.8h4.4c-.2 2.8-1.3 4.7-2.2 4.7s-2-1.9-2.2-4.7zM2.6 8.8h1.7c.1 1.8.5 3.3 1.1 4.3a5.5 5.5 0 0 1-2.8-4.3zm8.1 0h1.7a5.5 5.5 0 0 1-2.8 4.3c.6-1 1-2.5 1.1-4.3zM2.6 7.2a5.5 5.5 0 0 1 2.8-4.3c-.6 1-1 2.5-1.1 4.3zm8.1 0c-.1-1.8-.5-3.3-1.1-4.3a5.5 5.5 0 0 1 2.8 4.3z"/></svg>
          PrairieShingleWorks.com
        </li>
      </ul>
    </div>
  </section>

  <section class="card card--back" aria-label="Business card back">
    <div class="brand-lockup"><span class="brand-lockup__square"></span>BRENT Roofing &amp; Siding</div>
    <p class="slogan">BUILT <strong>TO LAST</strong>, BACKED <strong>BY OUR WORD</strong></p>
  </section>
</body>
</html>
```